Ridgeline Journeys business card

please see website
www.ridgelinejourneys.comau

info needed on card
Curtis Halvey
Ph
email
Adventure Riding GPS trails

please use my logo and colours off my site

Curtis Halvey
curtis@ridgelinejourneys.com

```html
<!DOCTYPE html>
<html lang="en">
<head>
<meta charset="utf-8">
<title>Ridgeline Journeys business card</title>
<link href="https://fonts.googleapis.com/css2?family=Open+Sans:wght@400;700;800&display=swap" rel="stylesheet">
<style>
  :root {
    --page: #e9e7e3;
    --card: #f2f1f2;
    --card-back: #ffffff;
    --yellow: #f7ec3c;
    --swoosh: #3d3f40;
    --ink: #1e1e1e;
    --rule: #555555;
    --mark: #dcdcdc;
  }
  * { box-sizing: border-box; margin: 0; padding: 0; }
  html, body { width: 1200px; height: 858px; overflow: hidden; }
  body {
    background: var(--page);
    font-family: "Open Sans", Arial, sans-serif;
    color: var(--ink);
    position: relative;
  }
  .card {
    position: absolute;
    top: 264px;
    width: 530px;
    height: 330px;
    overflow: hidden;
    box-shadow: 0 6px 18px rgba(0,0,0,.18);
  }
  .card-front { left: 50px; background: var(--card); }
  .card-back { left: 620px; background: var(--card-back); }
  .front-band { position: absolute; inset: 0; }
  .brand {
    position: absolute;
    font-weight: 800;
    text-transform: uppercase;
    line-height: 0.95;
    color: var(--ink);
  }
  .card-front .brand { left: 208px; top: 34px; font-size: 38px; letter-spacing: 1px; }
  .brand-dot {
    position: absolute;
    border-radius: 50%;
    background: var(--mark);
  }
  .card-front .brand-dot { left: 70px; top: 120px; width: 96px; height: 96px; }
  .holder-name {
    position: absolute;
    left: 208px; top: 150px;
    font-size: 25px; font-weight: 700;
  }
  .divider {
    position: absolute;
    left: 208px; right: 0; top: 196px;
    border-top: 1px solid var(--rule);
  }
  .contact {
    position: absolute;
    left: 208px; top: 210px;
    display: grid;
    grid-template-columns: 16px 1fr;
    column-gap: 10px;
    font-size: 15px; line-height: 1.3;
  }
  .contact .label {
    color: #bbbbbb;
    border-right: 1px solid #cccccc;
    padding-right: 4px;
  }
  .card-back .brand-dot { left: 215px; top: 60px; width: 100px; height: 100px; }
  .card-back .brand {
    left: 0; right: 0; top: 186px;
    text-align: center;
    font-size: 42px; letter-spacing: 1px;
  }
</style>
</head>
<body>
  <section class="card card-front" aria-label="Business card front">
    <svg class="front-band" width="530" height="330" viewBox="0 0 530 330" aria-hidden="true">
      <path d="M0 0 H150 C60 90 70 240 190 330 H0 Z" fill="var(--yellow)"/>
      <path d="M150 0 C60 90 70 240 190 330 H178 C50 240 46 90 134 0 Z" fill="var(--swoosh)"/>
    </svg>
    <span class="brand-dot" aria-hidden="true"></span>
    <h1 class="brand">Ridgeline<br>Journeys</h1>
    <p class="holder-name">Curtis Halvey</p>
    <hr class="divider">
    <div class="contact">
      <span class="label">E</span><span>curtis@ridgelinejourneys.com</span>
      <span class="label">W</span><span>www.ridgelinejourneys.comau</span>
    </div>
  </section>

  <section class="card card-back" aria-label="Business card back">
    <span class="brand-dot" aria-hidden="true"></span>
    <h2 class="brand">Ridgeline<br>Journeys</h2>
  </section>
</body>
</html>
```